Business Card Design - Property Management & Real Estate Services

I need a business card design for my company that I can print ZEPLA Cards. The company is called Brindle Management Company. It is a property management and real estate company. The design has to be clean and modern. I need two versions. One for my employee and one for me. However, the design will be the same, just different text. You can get a feel for the company by looking at our website at www.brindlemanagement.example.

Industry/Entity Type

Property Management

Contact Information for Business Card

I will be using ZEPLA.com to print my cards. I will most likely use the rounded edges card. I need two versions, however, they will be the same design. I need one for me and my employee.

Colors
3276b5
33a6d7

Requirements
Must have
• Company Logo
• Name of person
• Property Management & Real Estate Service
• Phone
• Email
• Website
• Address
• A space to place a QR code

```html
<!DOCTYPE html>
<html lang="en">
<head>
<meta charset="utf-8">
<title>Brindle Management – Business Card</title>
<link href="https://fonts.googleapis.com/css2?family=Roboto:wght@400;500&family=Exo+2:wght@700&display=swap" rel="stylesheet">
<style>
  :root{
    --page:#3a3b3e;
    --card:#1f2023;
    --silver:#b9bcc1;
    --blue-deep:#3276b5;
    --blue-light:#6aa7e2;
    --text-muted:#c7cbd1;
  }
  *{margin:0;padding:0;box-sizing:border-box}
  html,body{width:799px;height:1200px;overflow:hidden}
  body{background:var(--page);font-family:"Roboto",Arial,sans-serif;position:relative}
  .card{
    position:absolute;left:80px;width:640px;height:366px;
    background:var(--card);border-radius:24px;
    box-shadow:0 14px 30px rgba(0,0,0,.45);
    overflow:hidden;
  }
  .card--front{top:100px}
  .card--back{top:700px}

  .wordmark{font-family:"Roboto",Arial,sans-serif;font-weight:400;text-transform:uppercase;line-height:1}
  .card--front .wordmark{
    position:absolute;left:0;right:0;top:140px;text-align:center;color:var(--silver);
  }
  .card--front .wordmark__name{display:block;font-size:72px;letter-spacing:6px}
  .card--front .wordmark__sub{display:block;font-size:18px;letter-spacing:14px;margin-top:10px}

  .brand-decoration{
    position:absolute;left:34px;top:40px;width:230px;height:290px;
    border-radius:6px;
    background:linear-gradient(160deg,rgba(106,167,226,.55) 0%,rgba(50,118,181,.25) 55%,rgba(31,32,35,0) 100%);
  }

  .back-info{position:absolute;right:36px;top:40px;text-align:right;width:340px}
  .card--back .wordmark{color:var(--blue-deep)}
  .card--back .wordmark__name{display:block;font-size:50px;letter-spacing:4px}
  .card--back .wordmark__sub{display:block;font-size:13px;letter-spacing:10px;margin-top:6px}
  .rule{width:320px;height:2px;background:var(--blue-deep);margin:10px 0 0 auto}

  .person__name{font-family:"Exo 2",Arial,sans-serif;font-weight:700;font-size:23px;color:var(--blue-deep);margin-top:20px}
  .person__title{font-size:17px;color:var(--text-muted);margin-top:4px}

  .contact{list-style:none;margin-top:16px}
  .contact li{font-size:17px;color:var(--blue-light);line-height:27px;display:flex;justify-content:flex-end;align-items:center;gap:10px;white-space:nowrap}
  .contact svg{width:14px;height:14px;flex:none}
  .contact .spacer{width:14px;flex:none}
</style>
</head>
<body>

<section class="card card--front" aria-label="Card front">
  <div class="wordmark">
    <span class="wordmark__name">Brindle</span>
    <span class="wordmark__sub">Management</span>
  </div>
</section>

<section class="card card--back" aria-label="Card back">
  <div class="brand-decoration" role="img" aria-label="Large brand decoration in light blue line art"></div>

  <div class="back-info">
    <div class="wordmark">
      <span class="wordmark__name">Brindle</span>
      <span class="wordmark__sub">Management</span>
    </div>
    <div class="rule"></div>

    <p class="person__name">Tomas R. Delgado</p>
    <p class="person__title">Founder</p>

    <ul class="contact">
      <li>(555) 014-2290
        <svg viewBox="0 0 16 16" aria-hidden="true"><path fill="#3276b5" d="M3 1h3l1.5 4-2 1.2a9 9 0 0 0 4.3 4.3L11 8.5l4 1.5v3a2 2 0 0 1-2 2A13 13 0 0 1 1 3a2 2 0 0 1 2-2z"/></svg>
      </li>
      <li>tomas@brindlemanagement.example
        <svg viewBox="0 0 16 16" aria-hidden="true"><rect x="1" y="3" width="14" height="10" rx="1" fill="#3276b5"/><path d="M1.5 3.5 8 9l6.5-5.5" fill="none" stroke="#1f2023" stroke-width="1.3"/></svg>
      </li>
      <li>www.brindlemanagement.example
        <svg viewBox="0 0 16 16" aria-hidden="true"><circle cx="8" cy="8" r="6.5" fill="none" stroke="#3276b5" stroke-width="1.5"/><ellipse cx="8" cy="8" rx="2.6" ry="6.5" fill="none" stroke="#3276b5" stroke-width="1.2"/><path d="M1.5 8h13" stroke="#3276b5" stroke-width="1.2"/></svg>
      </li>
      <li>480 Harbor Ln #210 Bayview, FL 33000<span class="spacer"></span></li>
    </ul>
  </div>
</section>

</body>
</html>
```